Counseling Practice Business Card

I need a professional looking business card incorporating my new logo that was just completed. Card needs to incorporate my name and title, description of my specialty, my address, my phone number, my fax number, my email and my website URL. I need to be able to choose design on/with different paper colors and textures.
I do not have a lot of business card ideas so I am open to anything but I want bold,sharp, clear card without additional designs other than my logo (see attached file info). I am open to different color backgrounds or paper colors including black. I do not like traditional brackets around area codes in phone number or dashes between numbers in phone number. Am open to other ways of presenting including periods between numbers as appropriate. I do not know enough to know what I like yet but I want card to coordinate and work together with my logo. My practice emphasizes natural mental health interventions so any use of color (with background paper color or the blue and green in my logo) that elicits nature is nice. In addition to black, any natural brown or wood looking background might be desirable also. Most of the offerings so far look very similar and boring.

Target Market(s)

Potential therapy clients and other professionals

Contact Information for Business Card

Card information:
Gerald M. Whitcombe, Ph.D.
Licensed Clinical Psychologist
Integrative Health Coach
4812 Marlowe Ridge Blvd SE
Suite 310
Fernhollow, GA 30182
(770) 415-2983 phone
(770) 581-4096 fax
drgeraldwhitcombe@quillmarsh.net
brightfernwellness.net

Font styles to use
Serif
Sans Serif
Other font styles liked:
• anything that you think looks crisp, clear and easily readable

Requirements
Must have
• Any color used should coordinate with my logo design (see attached files).
• Card should be printed horizontally so top and bottom are longest sides of rectangle.
• Background color or paper color should complement and highlight logo. Do not like a white background. black, grey, brown or any color my logo would blend well with.
Nice to have
• I would like designer to utilize color to highlight letters/name or phone-fax-web symbols.
• Bottom edge of card could be highlighted if appropriate to an idea.
Should not have
• I would NOT want the card to have a pure white background at all.
• No clear cards.
• Cards should be oriented with long sides on bottom and top, NOT sides. DO NOT LIKE THIS THIN TALL ORIENTATION.

```html
<!DOCTYPE html>
<html lang="en">
<head>
<meta charset="utf-8">
<title>Brightfern Wellness – Business Card</title>
<link rel="stylesheet" href="https://fonts.googleapis.com/css2?family=Roboto:wght@400;500;700&display=swap">
<style>
  :root {
    --backdrop: #c8925c;
    --card-dark: #141519;
    --brand-blue: #2874b5;
    --name-blue: #2a72b8;
    --brand-green: #1c6a38;
    --band-text: #ffffff;
    --url-tint: #b3cbe3;
  }
  * { box-sizing: border-box; margin: 0; padding: 0; }
  html, body {
    width: 1200px; height: 960px; overflow: hidden;
    background: var(--backdrop);
    font-family: "Roboto", Arial, sans-serif;
  }
  .canvas { position: relative; width: 1200px; height: 960px; }
  .card {
    position: absolute; width: 600px; height: 344px;
    background: var(--card-dark); overflow: hidden;
    box-shadow: 0 3px 8px rgba(0,0,0,.35);
  }
  .card--front { left: 314px; top: 113px; }
  .card--back { left: 311px; top: 472px; height: 343px; }

  .identity { position: absolute; left: 30px; top: 78px; }
  .identity__name {
    color: var(--name-blue); font-weight: 500; font-size: 19.5px;
    letter-spacing: .2px; text-transform: uppercase; line-height: 24px;
  }
  .identity__role { color: var(--brand-green); font-size: 15px; line-height: 19px; font-weight: 500; }

  .brand { position: absolute; display: flex; align-items: center; }
  .brand__dot { border-radius: 50%; background: var(--brand-blue); flex: none; }
  .brand__name { color: var(--brand-blue); font-weight: 700; line-height: 1; }
  .card--front .brand { right: 34px; top: 80px; gap: 10px; }
  .card--front .brand__dot { width: 22px; height: 22px; }
  .card--front .brand__name { font-size: 28px; }
  .card--back .brand { left: 0; right: 0; top: 118px; justify-content: center; gap: 16px; }
  .card--back .brand__dot { width: 36px; height: 36px; }
  .card--back .brand__name { font-size: 48px; }

  .contact-band {
    position: absolute; left: 0; top: 208px; width: 600px; height: 136px;
    background: var(--brand-blue); color: var(--band-text); font-size: 14px;
  }
  .divider { position: absolute; left: 0; top: 202px; width: 600px; height: 18px; z-index: 1; }
  .contact-list { list-style: none; position: absolute; left: 30px; top: 29px; }
  .contact-list li { display: flex; align-items: center; gap: 8px; height: 19px; }
  .contact-list svg { width: 14px; height: 14px; fill: var(--band-text); flex: none; }
  .address {
    position: absolute; right: 34px; top: 52px; text-align: right;
    font-style: normal; line-height: 18px;
  }

  .url-band {
    position: absolute; left: 0; top: 279px; width: 600px; height: 30px;
    background: var(--brand-blue); color: var(--url-tint);
    font-size: 14px; letter-spacing: 3.6px; text-align: center; line-height: 30px;
  }
</style>
</head>
<body>
<div class="canvas">

  <section class="card card--front">
    <div class="identity">
      <p class="identity__name">Gerald M. Whitcombe, Ph.D.</p>
      <p class="identity__role">Licensed Clinical Psychologist</p>
      <p class="identity__role">Integrative Health Coach</p>
    </div>
    <div class="brand">
      <span class="brand__dot"></span>
      <span class="brand__name">Brightfern<br>Wellness</span>
    </div>
    <div class="contact-band">
      <ul class="contact-list">
        <li>
          <svg viewBox="0 0 16 16"><path d="M3.5 1.5l2.4 2.8-1.3 1.7c.9 2 2.5 3.6 4.5 4.5l1.7-1.3 2.8 2.4-1.4 2.2C6.8 13.4 2.6 9.2 1.3 3z"/></svg>
          (770) 415-2983
        </li>
        <li>
          <svg viewBox="0 0 16 16"><path d="M4 1h8v4H4zM1 6h14v6h-3v3H4v-3H1zM5 10v4h6v-4z"/></svg>
          (770) 581-4096
        </li>
        <li>
          <svg viewBox="0 0 16 16"><path d="M1 3h14v10H1zM2.5 4.5L8 9l5.5-4.5v-.1H2.5z"/></svg>
          drgeraldwhitcombe@quillmarsh.net
        </li>
        <li>
          <svg viewBox="0 0 16 16"><path d="M8 1a7 7 0 1 0 0 14A7 7 0 0 0 8 1zm-1 2.5l1.5 1-1 2 2 1.5v2l-2 2.5-1-3-2-1 .5-3z"/></svg>
          www.brightfernwellness.net
        </li>
      </ul>
      <address class="address">
        4812 Marlowe Ridge Blvd SE<br>
        Suite 310<br>
        Fernhollow, GA 30182
      </address>
    </div>
    <svg class="divider" viewBox="0 0 600 18" aria-hidden="true">
      <path d="M0 4.5 H74 L83 15 L92 4.5 H600" fill="#141519" stroke="#1c6a38" stroke-width="3"/>
    </svg>
  </section>

  <section class="card card--back">
    <div class="brand">
      <span class="brand__dot"></span>
      <span class="brand__name">Brightfern Wellness</span>
    </div>
    <div class="url-band">www.brightfernwellness.net</div>
  </section>

</div>
</body>
</html>
```